brovlanepass.net

Develop a website for brolanepass.net will be a site to sell tickets for concerts, shows, shows, theaters and others. I need a web design easy view, very easy to use and accumulate events by date. The aim is to develop the site was connected to a complex system that is already developed. (Important this page to a robust system was connected via links the idea is to develop only the front view)
Updates

Reason: I need more designs yet we have not made the decision

Target Market(s)

millennials, adults, who want to enjoy concerts and shows

Industry/Entity Type

Event

Number of Pages Required

5+ page

Colors
1b1b1b
aaaaaa
ffffff

Requirements
Must have
• Easy Vista, accumulation of upcoming events, past events. The tabs should have are: 1 Start: In this part of upcoming events occur. You could put a banner on the top and down the events by date. 2. How to order: page with instructions on how to purchase tickets 3. About Us: The company history 4. Contact: Phones and template for contact by mail 5. Our policies: shopping 6. Notice Privacy: Privacy Notice Copoy 7. Centers Sale: physical places where they can purchase tickets Promoters 8. access: Link to a template
Nice to have
• as you can see p www.quimbarostage.net or farunda.net or farunda.org or gallowmerk.net (important this page to a robust system was connected via links the idea is to develop only the front view)
Should not have
• Many things Tangled

```html
<!DOCTYPE html>
<html lang="en">
<head>
<meta charset="utf-8">
<title>Brovlane Pass</title>
<link href="https://fonts.googleapis.com/css2?family=Open+Sans:ital,wght@0,400;0,600;0,700;1,400;1,600&family=Raleway:wght@500;600;700;800&display=swap" rel="stylesheet">
<style>
:root{
  --ink:#1b1b1b;
  --panel:#222222;
  --band:#3a3a3a;
  --grey:#aaaaaa;
  --white:#ffffff;
  --orange:#f9a02a;
  --muted:#9a9a9a;
  --text-dark:#2a2a2a;
  --partner:#b9b9b9;
}
*{box-sizing:border-box;margin:0;padding:0}
html,body{width:1200px;height:2413px;overflow:hidden}
body{background:var(--ink);font-family:"Open Sans",Arial,sans-serif;color:var(--white);position:relative}
a{color:inherit;text-decoration:none}

/* top bar */
.topbar{position:absolute;top:0;left:0;width:1200px;height:35px;background:var(--ink);z-index:3}
.topbar .social{position:absolute;left:96px;top:11px;display:flex;gap:16px}
.topbar .social span{width:12px;height:12px;border-radius:2px;background:#d0d0d0;display:block}
.topbar .account{position:absolute;right:290px;top:0;height:35px;display:flex;align-items:center;gap:9px;font-size:14px}
.topbar .account i{display:inline-block;width:10px;height:10px;border-radius:50%;background:var(--orange);margin-right:5px;vertical-align:-1px}
.topbar .account .sep{color:#777}
.verified{position:absolute;right:100px;top:0;width:170px;height:35px;background:var(--grey);color:#fdd48e;font-style:italic;font-weight:600;font-size:15px;display:flex;align-items:center;justify-content:center;gap:7px}
.verified b{width:11px;height:11px;border-radius:50%;background:var(--orange);display:block}

/* hero */
.hero{position:absolute;top:0;left:0;width:1200px;height:521px}
.hero-photo{position:absolute;inset:0;background:
  radial-gradient(ellipse 30% 35% at 50% 25%,rgba(230,215,195,.55),rgba(0,0,0,0) 100%),
  radial-gradient(ellipse 12% 40% at 12% 40%,rgba(200,120,90,.35),rgba(0,0,0,0) 100%),
  radial-gradient(ellipse 12% 40% at 88% 40%,rgba(200,120,90,.35),rgba(0,0,0,0) 100%),
  linear-gradient(180deg,#3e342d 0%,#6a5a4e 30%,#3a2d25 62%,#1a1310 100%)}
.brand{position:absolute;left:100px;top:58px;display:flex;align-items:center;gap:10px}
.brand .mark{width:34px;height:34px;background:var(--orange)}
.brand .name{font-family:"Raleway",Arial,sans-serif;font-weight:700;font-size:23px;line-height:24px;color:var(--white)}
.nav{position:absolute;top:72px;right:98px;display:flex;gap:23px;font-size:16px;color:var(--white)}
.nav .active{color:var(--orange)}
.nav svg{margin-top:3px}
.hero h1{position:absolute;top:176px;width:100%;text-align:center;font-family:"Raleway",Arial,sans-serif;font-weight:800;font-size:70px;letter-spacing:3px}
.hero .lead{position:absolute;top:260px;width:100%;text-align:center;font-size:22px;color:#eeeeee}
.hero .btn-see{position:absolute;top:315px;left:523px;width:154px;height:38px;border:2px solid var(--white);border-radius:20px;background:rgba(0,0,0,.25);display:flex;align-items:center;justify-content:center;font-family:"Raleway",Arial,sans-serif;font-weight:700;font-size:14px}
.dots{position:absolute;top:469px;left:561px;display:flex;gap:6px}
.dots span{width:14px;height:14px;border-radius:50%;border:2px solid var(--white)}
.dots span.on{background:var(--white)}

/* categories */
.categories{position:absolute;top:521px;left:0;width:1200px;height:87px;background:var(--orange)}
.cat{position:absolute;top:13px;height:60px;display:flex;align-items:center;gap:22px;font-family:"Raleway",Arial,sans-serif;font-weight:700;font-size:17px;color:var(--white);border-right:1px solid rgba(255,255,255,.35)}
.cat-concerts{left:0;width:282px;padding-left:97px}
.cat-sports{left:282px;width:220px;padding-left:35px}
.cat-music{left:502px;width:200px;padding-left:39px}
.cat-theaters{left:702px;width:230px;padding-left:38px}
.cat-shows{left:932px;width:268px;padding-left:35px;border-right:none}

/* events */
.events{position:absolute;top:608px;left:0;width:1200px;height:1196px;background:var(--panel)}
.section-title{font-family:"Raleway",Arial,sans-serif;font-weight:700;font-size:30px;text-align:center;letter-spacing:.5px}
.events .section-title{position:absolute;top:65px;width:100%}
.grid{position:absolute;top:136px;left:98px;display:grid;grid-template-columns:repeat(3,320px);column-gap:22px;row-gap:26px}
.card{width:320px;height:287px;background:var(--white);border:3px solid var(--white);position:relative}
.card .photo{height:221px;width:100%}
.date{position:absolute;top:3px;left:3px;width:47px;padding:4px 0 6px 6px;background:rgba(20,20,20,.85);font-weight:700;font-size:14px;line-height:17px}
.card h3{font-family:"Raleway",Arial,sans-serif;font-weight:700;font-size:17px;color:var(--text-dark);margin:9px 0 0 13px}
.meta{display:flex;align-items:center;gap:6px;margin:6px 0 0 13px;font-size:12px;font-style:italic;color:var(--muted)}
.meta .bar{width:1px;height:12px;background:#ccc;margin:0 4px}
.view-more{position:absolute;top:1099px;left:513px;width:174px;height:38px;border:2px solid #666;border-radius:20px;display:flex;align-items:center;justify-content:center;color:var(--orange);font-weight:700;font-size:13px}

/* guides */
.guides{position:absolute;top:1804px;left:0;width:1200px;height:263px;background:var(--band)}
.guides .section-title{position:absolute;top:50px;width:100%}
.guide-row{position:absolute;top:124px;left:98px;display:flex;gap:15px}
.guide{width:189px;height:80px;background:var(--white);display:flex;align-items:center;justify-content:center}
.guide span{width:140px;height:30px;background:var(--partner);border-radius:3px}
.arrow{position:absolute;top:150px}
.arrow.left{left:58px}.arrow.right{left:1124px}

/* footer */
.footer{position:absolute;top:2067px;left:0;width:1200px;height:346px;background:var(--ink)}
.col{position:absolute;top:59px}
.col h4{font-family:"Raleway",Arial,sans-serif;font-weight:700;font-size:15px;margin-bottom:14px;letter-spacing:.3px}
.col li{list-style:none;font-size:12px;line-height:26.7px;color:#dddddd}
.col-help li{line-height:30px}
.col-resources{left:98px}.col-help{left:328px}.col-links{left:579px}.col-mail{left:777px;width:325px}
.col-mail p{font-size:12px;color:#dddddd;margin-bottom:14px}
.subscribe{display:flex;height:36px}
.subscribe .field{flex:1;background:var(--white);color:#999;font-size:12px;padding-left:14px;display:flex;align-items:center}
.subscribe .go{width:94px;background:var(--orange);font-weight:700;font-size:12px;display:flex;align-items:center;justify-content:center}
.col-mail h4.stay{margin-top:20px;margin-bottom:18px}
.round-row{display:flex;gap:9px}
.round-row span{width:34px;height:34px;border-radius:50%;display:block}
.copyright{position:absolute;top:303px;width:100%;text-align:center;font-size:12px;color:#dddddd}
</style>
</head>
<body>

<header class="topbar">
  <div class="social"><span></span><span></span><span></span><span></span><span></span><span></span></div>
  <nav class="account">
    <a href="#"><i></i>Help</a><span class="sep">|</span>
    <a href="#"><i></i>My account</a><span class="sep">|</span>
    <a href="#"><i></i>Sign up</a>
  </nav>
  <div class="verified"><b></b>Verified Tickets</div>
</header>

<section class="hero">
  <div class="hero-photo" role="img" aria-label="Concert crowd with raised hands under stage lights"></div>
  <div class="brand"><span class="mark"></span><span class="name">Brovlane<br>Pass</span></div>
  <nav class="nav">
    <a class="active" href="#">Home</a><a href="#">How to Order</a><a href="#">About us</a><a href="#">Contact us</a><a href="#">Policies</a><a href="#">Privacy</a><a href="#">Center Sale</a><a href="#">Access</a>
    <svg width="14" height="14" viewBox="0 0 14 14"><circle cx="6" cy="6" r="4.5" fill="none" stroke="#fff" stroke-width="2"/><line x1="9.5" y1="9.5" x2="13" y2="13" stroke="#fff" stroke-width="2"/></svg>
  </nav>
  <h1>BROVLANE PASS</h1>
  <p class="lead">We want a site to sell tickets for concerts, shows, theaters and others</p>
  <a class="btn-see" href="#">SEE TICKETS</a>
  <div class="dots"><span class="on"></span><span></span><span></span><span></span></div>
</section>

<nav class="categories">
  <a class="cat cat-concerts" href="#"><svg width="26" height="40" viewBox="0 0 26 40"><rect x="7" y="2" width="12" height="22" rx="6" fill="#fff"/><path d="M3 18a10 10 0 0 0 20 0" fill="none" stroke="#fff" stroke-width="2.5"/><rect x="11.5" y="28" width="3" height="8" fill="#fff"/><rect x="6" y="36" width="14" height="3" fill="#fff"/></svg>CONCERTS</a>
  <a class="cat cat-sports" href="#"><svg width="46" height="46" viewBox="0 0 46 46"><circle cx="23" cy="23" r="21" fill="#fff"/><polygon points="23,14 31,20 28,29 18,29 15,20" fill="#f9a02a"/></svg>SPORTS</a>
  <a class="cat cat-music" href="#"><svg width="40" height="42" viewBox="0 0 40 42"><path d="M12 6 L36 1 V30" fill="none" stroke="#fff" stroke-width="4"/><line x1="12" y1="6" x2="12" y2="35" stroke="#fff" stroke-width="4"/><ellipse cx="7" cy="35" rx="6.5" ry="5" fill="#fff"/><ellipse cx="31" cy="30" rx="6.5" ry="5" fill="#fff"/></svg>MUSIC</a>
  <a class="cat cat-theaters" href="#"><svg width="48" height="34" viewBox="0 0 48 34"><rect x="0" y="2" width="32" height="30" rx="4" fill="#fff"/><polygon points="34,12 48,3 48,31 34,22" fill="#fff"/></svg>THEATERS</a>
  <a class="cat cat-shows" href="#"><svg width="44" height="44" viewBox="0 0 44 44"><line x1="4" y1="40" x2="28" y2="16" stroke="#fff" stroke-width="5"/><path d="M33 3l2 5 5 2-5 2-2 5-2-5-5-2 5-2z" fill="#fff"/><circle cx="20" cy="7" r="2" fill="#fff"/><circle cx="38" cy="24" r="2" fill="#fff"/></svg>SHOWS</a>
</nav>

<section class="events">
  <h2 class="section-title">UPCOMING EVENTS</h2>
  <div class="grid">
    <article class="card"><div class="photo" role="img" aria-label="Guitarist performing to a reaching crowd" style="background:radial-gradient(ellipse at 80% 20%,#e0b07a,rgba(0,0,0,0) 55%),linear-gradient(135deg,#2a1a10,#7a4e2e 55%,#3a2414)"></div><div class="date">26<br>nov<br>2017</div><h3>Finibus Bonorum et Malorum</h3><div class="meta"><svg width="10" height="10"><circle cx="5" cy="5" r="4" fill="none" stroke="#f9a02a" stroke-width="1.5"/></svg>10:00 PM<span class="bar"></span><svg width="8" height="11"><path d="M4 0a4 4 0 0 1 4 4c0 3-4 7-4 7S0 7 0 4a4 4 0 0 1 4-4z" fill="#f9a02a"/></svg>Blanditiis pra</div></article>
    <article class="card"><div class="photo" role="img" aria-label="Band on a brightly lit stage with colored lights" style="background:radial-gradient(ellipse at 50% 25%,#ffd27a,rgba(0,0,0,0) 50%),linear-gradient(180deg,#e08a3a,#a8405a 50%,#24248a 85%,#101040)"></div><div class="date">26<br>nov<br>2017</div><h3>Finibus Bonorum et Malorum</h3><div class="meta"><svg width="10" height="10"><circle cx="5" cy="5" r="4" fill="none" stroke="#f9a02a" stroke-width="1.5"/></svg>10:00 PM<span class="bar"></span><svg width="8" height="11"><path d="M4 0a4 4 0 0 1 4 4c0 3-4 7-4 7S0 7 0 4a4 4 0 0 1 4-4z" fill="#f9a02a"/></svg>Blanditiis pra</div></article>
    <article class="card"><div class="photo" role="img" aria-label="Dance troupe in red costumes on a dark stage" style="background:radial-gradient(ellipse 45% 35% at 50% 55%,#b4544a,#4a1a14 60%,#050303 100%)"></div><div class="date">26<br>nov<br>2017</div><h3>Finibus Bonorum et Malorum</h3><div class="meta"><svg width="10" height="10"><circle cx="5" cy="5" r="4" fill="none" stroke="#f9a02a" stroke-width="1.5"/></svg>10:00 PM<span class="bar"></span><svg width="8" height="11"><path d="M4 0a4 4 0 0 1 4 4c0 3-4 7-4 7S0 7 0 4a4 4 0 0 1 4-4z" fill="#f9a02a"/></svg>Blanditiis pra</div></article>
    <article class="card"><div class="photo" role="img" aria-label="Singer in a hat holding a guitar" style="background:radial-gradient(ellipse at 40% 45%,#8a7aa8,rgba(0,0,0,0) 50%),linear-gradient(135deg,#20226a,#3a3a90 50%,#101030)"></div><div class="date">26<br>nov<br>2017</div><h3>Finibus Bonorum et Malorum</h3><div class="meta"><svg width="10" height="10"><circle cx="5" cy="5" r="4" fill="none" stroke="#f9a02a" stroke-width="1.5"/></svg>10:00 PM<span class="bar"></span><svg width="8" height="11"><path d="M4 0a4 4 0 0 1 4 4c0 3-4 7-4 7S0 7 0 4a4 4 0 0 1 4-4z" fill="#f9a02a"/></svg>Blanditiis pra</div></article>
    <article class="card"><div class="photo" role="img" aria-label="Brass band playing saxophones on stage" style="background:radial-gradient(ellipse at 50% 45%,#8a8494,rgba(0,0,0,0) 60%),linear-gradient(135deg,#1e1e24,#4a4654 50%,#18181c)"></div><div class="date">26<br>nov<br>2017</div><h3>Finibus Bonorum et Malorum</h3><div class="meta"><svg width="10" height="10"><circle cx="5" cy="5" r="4" fill="none" stroke="#f9a02a" stroke-width="1.5"/></svg>10:00 PM<span class="bar"></span><svg width="8" height="11"><path d="M4 0a4 4 0 0 1 4 4c0 3-4 7-4 7S0 7 0 4a4 4 0 0 1 4-4z" fill="#f9a02a"/></svg>Blanditiis pra</div></article>
    <article class="card"><div class="photo" role="img" aria-label="DJ at a mixing deck in front of a crowd" style="background:radial-gradient(ellipse at 30% 20%,#e08a3a,rgba(0,0,0,0) 60%),linear-gradient(160deg,#8a3a1a,#4a1e12 50%,#141010)"></div><div class="date">26<br>nov<br>2017</div><h3>Finibus Bonorum et Malorum</h3><div class="meta"><svg width="10" height="10"><circle cx="5" cy="5" r="4" fill="none" stroke="#f9a02a" stroke-width="1.5"/></svg>10:00 PM<span class="bar"></span><svg width="8" height="11"><path d="M4 0a4 4 0 0 1 4 4c0 3-4 7-4 7S0 7 0 4a4 4 0 0 1 4-4z" fill="#f9a02a"/></svg>Blanditiis pra</div></article>
    <article class="card"><div class="photo" role="img" aria-label="Two magicians performing an escape act with chains" style="background:radial-gradient(ellipse at 25% 70%,#a01818,rgba(0,0,0,0) 45%),linear-gradient(90deg,#141414,#2a1a1a 50%,#262626)"></div><div class="date">26<br>nov<br>2017</div><h3>Finibus Bonorum et Malorum</h3><div class="meta"><svg width="10" height="10"><circle cx="5" cy="5" r="4" fill="none" stroke="#f9a02a" stroke-width="1.5"/></svg>10:00 PM<span class="bar"></span><svg width="8" height="11"><path d="M4 0a4 4 0 0 1 4 4c0 3-4 7-4 7S0 7 0 4a4 4 0 0 1 4-4z" fill="#f9a02a"/></svg>Blanditiis pra</div></article>
    <article class="card"><div class="photo" role="img" aria-label="Horror theater scene with costumed actors" style="background:radial-gradient(ellipse at 60% 30%,#b8a890,rgba(0,0,0,0) 55%),linear-gradient(135deg,#4a3c30,#7a6a58 50%,#2e241c)"></div><div class="date">26<br>nov<br>2017</div><h3>Finibus Bonorum et Malorum</h3><div class="meta"><svg width="10" height="10"><circle cx="5" cy="5" r="4" fill="none" stroke="#f9a02a" stroke-width="1.5"/></svg>10:00 PM<span class="bar"></span><svg width="8" height="11"><path d="M4 0a4 4 0 0 1 4 4c0 3-4 7-4 7S0 7 0 4a4 4 0 0 1 4-4z" fill="#f9a02a"/></svg>Blanditiis pra</div></article>
    <article class="card"><div class="photo" role="img" aria-label="Dancer in flowing orange fabric" style="background:radial-gradient(ellipse at 40% 45%,#f08a44,rgba(0,0,0,0) 55%),linear-gradient(135deg,#1a0806,#b83a16 50%,#2a0a06)"></div><div class="date">26<br>nov<br>2017</div><h3>Finibus Bonorum et Malorum</h3><div class="meta"><svg width="10" height="10"><circle cx="5" cy="5" r="4" fill="none" stroke="#f9a02a" stroke-width="1.5"/></svg>10:00 PM<span class="bar"></span><svg width="8" height="11"><path d="M4 0a4 4 0 0 1 4 4c0 3-4 7-4 7S0 7 0 4a4 4 0 0 1 4-4z" fill="#f9a02a"/></svg>Blanditiis pra</div></article>
  </div>
  <a class="view-more" href="#">VIEW MORE &gt;&gt;</a>
</section>

<section class="guides">
  <h2 class="section-title">ENTERTAINMENT GUIDES</h2>
  <svg class="arrow left" width="18" height="28" viewBox="0 0 18 28"><polyline points="15,2 3,14 15,26" fill="none" stroke="#999" stroke-width="3"/></svg>
  <div class="guide-row">
    <div class="guide"><span></span></div>
    <div class="guide"><span></span></div>
    <div class="guide"><span></span></div>
    <div class="guide"><span></span></div>
    <div class="guide"><span></span></div>
  </div>
  <svg class="arrow right" width="18" height="28" viewBox="0 0 18 28"><polyline points="3,2 15,14 3,26" fill="none" stroke="#999" stroke-width="3"/></svg>
</section>

<footer class="footer">
  <div class="col col-resources"><h4>RESOURCES</h4><ul><li>Your Account</li><li>Transfer or Sell Tickets</li><li>Print Tickets</li><li>FAQs</li><li>Refunds and Exchanges</li><li>Get Help</li></ul></div>
  <div class="col col-help"><h4>HELP &amp; SUPPORT</h4><ul><li>Recommended Reading</li><li>Submit your Story</li><li>Contact Us</li><li>Frequently Asked Questions</li><li>How to Order</li></ul></div>
  <div class="col col-links"><h4>QUICK LINKS</h4><ul><li>Halvero Live</li><li>Marrow Hall</li><li>Tesslyweb</li><li>PonderaNow</li><li>Quillmo</li><li>ostrava</li></ul></div>
  <div class="col col-mail">
    <h4>EMAIL SUBSCRIPTION</h4>
    <p>Register your email address to get information about us</p>
    <div class="subscribe"><span class="field">Email Address</span><span class="go">SUBSCRIBE</span></div>
    <h4 class="stay">STAY CONNECTED</h4>
    <div class="round-row">
      <span style="background:#2aa36a"></span><span style="background:#3b5998"></span><span style="background:#2aa9e0"></span><span style="background:#dd4b39"></span><span style="background:#4a7ab0"></span><span style="background:#4aa3df"></span><span style="background:#cc181e"></span><span style="background:#cb2027"></span>
    </div>
  </div>
  <p class="copyright">Copyrights © 2017, Brovlane Pass. All Rights Reserved &nbsp;| &nbsp;Privacy Policy | Terms of Use | Feedback</p>
</footer>

</body>
</html>
```